Meridale Nutrition needs Stationary and a business card

We would like to use our current logo. The text can be moved around as needed. The stationary needs to be a 'first page' where the logo is more prominent to be impressive on higher quality paper and a second page where the logo is more subtle where there will be much more information on the page. There are 2 clinic locations which will need include name, address, phone number, fax number, web address. The business card should be single sided and contain this information also.
The design must be contemporary and sophisticated as this is a science based diet run out of a medical clinic.

Target Market(s)

People wanting to lose weight, athletes looking to optimise performance, people with arthritis or fighting cancer

Industry/Entity Type

Business

Contact Information for Business Card

must use the logo. I have attached an example card with the practice details on it. there must be space for the doctors name. Also the website www.meridalenutrition.com.au

Requirements
Must have
• the logo, the business adresses and phone numbers, the website, the doctors name and qualifications
Nice to have
• some creativity
Should not have
• Do not simply reproduce the existing card please

```html
<!DOCTYPE html>
<html lang="en">
<head>
<meta charset="utf-8">
<title>Meridale Nutrition – Business Card</title>
<link href="https://fonts.googleapis.com/css2?family=Arimo:wght@400;700&display=swap" rel="stylesheet">
<style>
  :root {
    --page-bg: #e9edf1;
    --card-white: #ffffff;
    --navy: #1f4c7e;
    --navy-deep: #1a416d;
    --back-navy: #22507f;
    --back-steel: #3f6a96;
    --sky: #3fb4df;
    --sky-light: #6fcbe9;
    --accent: #27a6de;
    --ink: #3a3f45;
    --band-text: #e8f4fb;
  }
  html, body {
    margin: 0;
    width: 1200px;
    height: 950px;
    overflow: hidden;
    background: var(--page-bg);
    font-family: "Arimo", Arial, sans-serif;
  }
  .card {
    position: absolute;
    width: 760px;
    height: 440px;
    overflow: hidden;
    box-shadow: 0 10px 30px rgba(20, 40, 70, 0.22);
  }

  /* Back side */
  .card-back {
    left: 340px;
    top: 70px;
    background: linear-gradient(100deg, var(--navy-deep) 0%, var(--back-navy) 55%, var(--back-steel) 100%);
  }
  .back-brand {
    position: absolute;
    left: 60px;
    top: 70px;
    display: flex;
    align-items: center;
    gap: 16px;
  }
  .back-brand .brand-dot { background: var(--sky); }
  .back-brand .brand-name { color: #ffffff; }
  .back-web {
    position: absolute;
    left: 132px;
    top: 134px;
    margin: 0;
    font-size: 15px;
    color: var(--sky-light);
  }

  /* Front side */
  .card-front {
    left: 100px;
    top: 420px;
    background: var(--card-white);
  }
  .doctor {
    position: absolute;
    left: 46px;
    top: 34px;
    color: var(--ink);
  }
  .doctor-name {
    margin: 0;
    font-size: 27px;
    font-weight: 700;
    color: var(--navy);
  }
  .doctor-credentials {
    margin: 6px 0 0;
    font-size: 14px;
    line-height: 1.3;
    color: var(--accent);
  }
  .services {
    margin: 14px 0 0;
    padding: 0;
    list-style: none;
    font-size: 16px;
    line-height: 1.35;
  }
  .services .service-gap { margin-top: 6px; }

  .brand {
    display: flex;
    align-items: center;
    gap: 14px;
    white-space: nowrap;
  }
  .brand-dot {
    flex: none;
    width: 56px;
    height: 56px;
    border-radius: 50%;
    background: var(--sky);
  }
  .brand-name {
    font-size: 28px;
    font-weight: 700;
    color: var(--navy);
    line-height: 1;
  }
  .front-brand {
    position: absolute;
    left: 400px;
    top: 120px;
  }
  .front-web {
    position: absolute;
    left: 470px;
    top: 182px;
    margin: 0;
    font-size: 14px;
    color: var(--accent);
  }

  .location-band {
    position: absolute;
    left: 0;
    bottom: 0;
    width: 760px;
    height: 185px;
    background: linear-gradient(90deg, var(--navy-deep) 0%, var(--navy) 38%, var(--sky) 62%, var(--sky-light) 100%);
  }
  .band-decoration {
    position: absolute;
    left: 250px;
    top: 0;
    width: 130px;
    height: 185px;
    background: linear-gradient(180deg, rgba(255,255,255,0.22), rgba(255,255,255,0.06));
  }
  .clinic {
    position: absolute;
    font-size: 15px;
    font-style: normal;
    line-height: 1.35;
    color: var(--band-text);
  }
  .clinic-easthaven { left: 46px; top: 20px; }
  .clinic-westbrook { right: 46px; bottom: 18px; text-align: right; }
  .clinic-name {
    display: block;
    font-weight: 700;
    color: var(--sky-light);
  }
  .clinic-westbrook .clinic-name { color: #ffffff; }
  .clinic-label { font-weight: 700; color: var(--sky-light); }
  .clinic-westbrook .clinic-label { color: #ffffff; }
</style>
</head>
<body>
  <section class="card card-back" aria-label="Card back">
    <div class="brand back-brand">
      <span class="brand-dot" aria-hidden="true"></span>
      <span class="brand-name">Meridale Nutrition</span>
    </div>
    <p class="back-web">www.meridalenutrition.com.au</p>
  </section>

  <article class="card card-front" aria-label="Card front">
    <header class="doctor">
      <h1 class="doctor-name">Dr Adrian Vell</h1>
      <p class="doctor-credentials">MBBS (NSW) MBiomedE FRACS (Ortho) FAOrthA<br>Orthopaedic Surgeon</p>
      <ul class="services">
        <li>Knee surgery</li>
        <li>www.jointclinicsydney.com.au</li>
        <li class="service-gap">Shoulder and Elbow</li>
        <li>www.adrianvell.com.au</li>
      </ul>
    </header>

    <div class="brand front-brand">
      <span class="brand-dot" aria-hidden="true"></span>
      <span class="brand-name">Meridale Nutrition</span>
    </div>
    <p class="front-web">www.meridalenutrition.com.au</p>

    <section class="location-band">
      <div class="band-decoration" role="img" aria-label="Decorative silhouette of a figure with raised arms"></div>
      <address class="clinic clinic-easthaven">
        <span class="clinic-name">Easthaven</span>
        12-14 Harbour Road<br>
        Easthaven NSW 2140<br>
        <span class="clinic-label">Tel:</span> 02 9000 1234<br>
        <span class="clinic-label">Fax:</span> 02 9000 1235
      </address>
      <address class="clinic clinic-westbrook">
        <span class="clinic-name">Westbrook</span>
        88 Linden Road<br>
        Westbrook NSW 2035<br>
        <span class="clinic-label">Tel:</span> 02 9000 5678<br>
        <span class="clinic-label">Fax:</span> 02 9000 5679
      </address>
    </section>
  </article>
</body>
</html>
```